Business Card Design Project

Doctor, Pain Management. Need a new business card design with appointment info on the back. New address is 18 Corvell Road, Suite 304, Brisdale, NJ 07391. Right now I believe the rest of the information is staying the same.

```html
<!DOCTYPE html>
<html lang="en">
<head>
<meta charset="utf-8">
<title>Steadfast Pain Care – Business Card</title>
<link href="https://fonts.googleapis.com/css2?family=Open+Sans:ital,wght@0,400;0,600;0,700;1,400&display=swap" rel="stylesheet">
<style>
  :root {
    --orange: #e85a0e;
    --card-grey: #dedede;
    --panel-light: #efeded;
    --ink: #2e2e2e;
    --rule: #a9a9a9;
    --stage: #3a3b3d;
    --white: #ffffff;
  }
  * { box-sizing: border-box; margin: 0; padding: 0; }
  html, body { width: 1200px; height: 896px; overflow: hidden; }
  body {
    background: var(--stage);
    font-family: "Open Sans", Arial, sans-serif;
    color: var(--ink);
    display: flex;
    flex-direction: column;
    align-items: center;
    justify-content: center;
    gap: 40px;
  }
  .card {
    position: relative;
    width: 700px;
    height: 400px;
    overflow: hidden;
    box-shadow: 0 6px 18px rgba(0,0,0,.35);
  }

  /* Front */
  .card-front { background: var(--card-grey); }
  .brand {
    position: absolute; right: 48px; top: 56px;
    color: var(--orange);
    font-size: 40px; font-weight: 400; line-height: 1;
    letter-spacing: .5px;
    padding-bottom: 8px;
    border-bottom: 2px solid var(--orange);
  }
  .doctor { position: absolute; left: 48px; top: 150px; }
  .doctor-name {
    color: var(--orange); font-weight: 700; font-size: 19px;
    text-transform: uppercase; letter-spacing: .3px;
  }
  .doctor-title { font-size: 15px; margin-top: 2px; }
  .doctor-rule {
    position: absolute; left: 48px; right: 48px; top: 205px;
    height: 1px; background: var(--rule);
  }
  .address { position: absolute; left: 48px; top: 230px; font-size: 15px; line-height: 1.45; }
  .contacts {
    position: absolute; right: 48px; bottom: 40px;
    list-style: none; text-align: right; font-size: 15px; line-height: 1.6;
  }
  .contacts li { display: flex; align-items: center; justify-content: flex-end; gap: 8px; }
  .contacts svg { width: 14px; height: 14px; flex: none; }

  /* Back */
  .card-back { background: var(--orange); }
  .back-heading {
    position: absolute; right: 44px; top: 28px;
    color: var(--white); font-size: 26px; font-weight: 600;
  }
  .form-panel {
    position: absolute; left: 0; right: 0; top: 96px; height: 206px;
    background: var(--panel-light);
    padding: 30px 44px 0;
    font-size: 17px;
  }
  .field { display: flex; align-items: baseline; gap: 8px; margin-bottom: 14px; }
  .field .dots { flex: 1; border-bottom: 2px dotted #555; height: 1px; }
  .field-row { display: flex; gap: 24px; }
  .field-row .field { flex: 1; }
  .ampm { white-space: nowrap; }
  .days { display: flex; gap: 26px; margin-top: 14px; list-style: none; }
  .days li { display: flex; align-items: center; gap: 7px; font-size: 16px; }
  .box { width: 18px; height: 18px; border: 1.5px solid #555; background: var(--white); }
  .back-note {
    position: absolute; left: 44px; right: 44px; bottom: 38px;
    color: var(--white); font-style: italic; font-size: 15px;
  }
</style>
</head>
<body>

<section class="card card-front" aria-label="Business card front">
  <div class="brand">Steadfast Pain Care</div>
  <div class="doctor">
    <p class="doctor-name">Dr. Weilin Shao, M.D., Ph.D</p>
    <p class="doctor-title">Board Certified Anesthesiologist</p>
  </div>
  <div class="doctor-rule"></div>
  <address class="address" style="font-style:normal">
    18 Corvell Road, Suite 304<br>Brisdale, NJ 07391
  </address>
  <ul class="contacts">
    <li>973.555.0148
      <svg viewBox="0 0 14 14"><circle cx="7" cy="7" r="7" fill="#e85a0e"/><path d="M4 4.5c0 3 2.5 5.5 5.5 5.5l.8-1.4-1.6-1-.8.7c-.9-.4-1.7-1.2-2.1-2.1l.7-.8-1-1.6z" fill="#fff"/></svg></li>
    <li>973.555.0149
      <svg viewBox="0 0 14 14"><circle cx="7" cy="7" r="7" fill="#e85a0e"/><rect x="4.5" y="3.5" width="5" height="3" fill="#fff"/><rect x="3.5" y="6.5" width="7" height="4" rx=".6" fill="#fff"/></svg></li>
    <li>www.steadfastpc.com
      <svg viewBox="0 0 14 14"><circle cx="7" cy="7" r="7" fill="#e85a0e"/><circle cx="7" cy="7" r="3.6" fill="none" stroke="#fff" stroke-width="1"/><path d="M3.4 7h7.2M7 3.4c-1.8 2-1.8 5.2 0 7.2M7 3.4c1.8 2 1.8 5.2 0 7.2" fill="none" stroke="#fff" stroke-width=".8"/></svg></li>
    <li>steadfastpc.office@mail.com
      <svg viewBox="0 0 14 14"><circle cx="7" cy="7" r="7" fill="#e85a0e"/><rect x="3.5" y="4.5" width="7" height="5" fill="#fff"/><path d="M3.5 4.5 7 7.3l3.5-2.8" fill="none" stroke="#e85a0e" stroke-width=".8"/></svg></li>
  </ul>
</section>

<section class="card card-back" aria-label="Business card back">
  <h2 class="back-heading">Your Next Appointment on</h2>
  <div class="form-panel">
    <div class="field"><span>Name :</span><span class="dots"></span></div>
    <div class="field-row">
      <div class="field"><span>Date :</span><span class="dots"></span></div>
      <div class="field"><span>Time :</span><span class="dots"></span><span class="ampm">AM / PM</span></div>
    </div>
    <ul class="days">
      <li><span class="box"></span>MON</li>
      <li><span class="box"></span>TUE</li>
      <li><span class="box"></span>WED</li>
      <li><span class="box"></span>THU</li>
      <li><span class="box"></span>FRI</li>
      <li><span class="box"></span>SAT</li>
    </ul>
  </div>
  <p class="back-note">If unable to keep your appointment, please contact us as soon as possible</p>
</section>

</body>
</html>
```